Business Card Design Project

Business Card
We are rebranding with a new logo
Industry/Entity Type
Business
Contact Information for Business Card
Dennis Morvale +61 487215963 dennis@quorv.com.au P.O. Box 872 Fernlow QLD 4309
Requirements
Must have
- Logo

```html
<!DOCTYPE html>
<html lang="en">
<head>
<meta charset="utf-8">
<title>Quorv International – Business Card</title>
<link rel="stylesheet" href="https://fonts.googleapis.com/css2?family=Roboto:wght@400;500;700&family=Roboto+Condensed:wght@700&display=swap">
<style>
  :root {
    --backdrop: #262626;
    --card: #f3f3f3;
    --brand-blue: #0f78a8;
    --band-blue-light: #0aa0d6;
    --band-blue-dark: #0b5f86;
    --accent-orange: #e87a1e;
    --accent-orange-dark: #d0601a;
    --text-light: #ffffff;
  }
  * { margin: 0; padding: 0; box-sizing: border-box; }
  html, body {
    width: 1200px;
    height: 960px;
    overflow: hidden;
    background: var(--backdrop);
  }
  .canvas {
    position: relative;
    width: 1200px;
    height: 960px;
  }
  .business-card {
    position: absolute;
    left: 223px;
    top: 265px;
    width: 754px;
    height: 430px;
    border-radius: 20px;
    overflow: hidden;
    background: var(--card);
    font-family: "Roboto", Arial, sans-serif;
  }
  .card-waves {
    position: absolute;
    inset: 0;
    width: 754px;
    height: 430px;
  }
  .brand-name {
    position: absolute;
    left: 64px;
    top: 78px;
    color: var(--brand-blue);
    font-family: "Roboto", Arial, sans-serif;
    font-weight: 500;
    line-height: 1;
  }
  .brand-name .brand-main {
    display: block;
    font-size: 84px;
    letter-spacing: 1px;
  }
  .brand-name .brand-sub {
    display: block;
    margin-top: 22px;
    font-size: 22px;
    letter-spacing: 3.2px;
  }
  .holder-name {
    position: absolute;
    right: 35px;
    top: 285px;
    font-family: "Roboto Condensed", "Arial Narrow", sans-serif;
    font-weight: 700;
    font-size: 26px;
    color: var(--accent-orange);
    letter-spacing: 0.3px;
  }
  .postal-address {
    position: absolute;
    right: 276px;
    top: 356px;
    text-align: right;
    color: var(--text-light);
    font-size: 17px;
    line-height: 23px;
    font-style: normal;
  }
  .contact-divider {
    position: absolute;
    left: 503px;
    top: 357px;
    width: 1px;
    height: 42px;
    background: rgba(255,255,255,0.85);
  }
  .contact-list {
    position: absolute;
    right: 35px;
    top: 330px;
    list-style: none;
    color: var(--text-light);
    font-size: 17px;
    line-height: 24px;
    text-align: right;
  }
  .contact-list li {
    display: flex;
    justify-content: flex-end;
    align-items: center;
    gap: 7px;
  }
  .contact-icon {
    width: 15px;
    height: 15px;
    flex: none;
  }
</style>
</head>
<body>
<div class="canvas">
  <section class="business-card">
    <svg class="card-waves" viewBox="0 0 754 430" aria-hidden="true">
      <defs>
        <radialGradient id="bandBlue" cx="0.55" cy="0.65" r="0.7">
          <stop offset="0" stop-color="var(--band-blue-light)"/>
          <stop offset="1" stop-color="var(--band-blue-dark)"/>
        </radialGradient>
      </defs>
      <path d="M2,426 Q290,236 735,231 Q310,250 14,430 Z" fill="var(--accent-orange)"/>
      <path d="M8,430 Q300,244 754,240 L754,246 Q305,254 14,430 Z" fill="var(--accent-orange-dark)"/>
      <path d="M12,430 Q300,250 754,242 L754,430 Z" fill="#ffffff"/>
      <path d="M20,430 Q305,256 754,246 L754,430 Z" fill="url(#bandBlue)"/>
    </svg>

    <h1 class="brand-name">
      <span class="brand-main">Quorv</span>
      <span class="brand-sub">INTERNATIONAL</span>
    </h1>

    <h2 class="holder-name">DENNIS MORVALE</h2>

    <address class="postal-address">P.O. Box 872<br>Fernlow QLD 4309</address>

    <div class="contact-divider"></div>

    <ul class="contact-list">
      <li>+61 487215963
        <svg class="contact-icon" viewBox="0 0 16 16" aria-hidden="true"><path fill="var(--accent-orange)" d="M3.6 1.2l2.3 2.6c.4.4.3 1-.1 1.4L4.7 6.1c.9 2 2.7 3.9 5.2 5.2l.9-1.1c.4-.4 1-.5 1.4-.1l2.6 2.3c.4.4.4 1 0 1.4l-1.3 1.3c-.6.6-1.5.8-2.3.5C6.1 14 2 9.9.4 4.8.1 4 .3 3.1.9 2.5L2.2 1.2c.4-.4 1-.4 1.4 0z"/></svg>
      </li>
      <li>dennis@quorv.com.au
        <svg class="contact-icon" viewBox="0 0 16 16" aria-hidden="true"><rect x="0.5" y="3" width="15" height="10.5" rx="1.5" fill="var(--accent-orange)"/><path d="M1.5 4.5L8 9l6.5-4.5" stroke="#0b6b96" stroke-width="1.2" fill="none"/></svg>
      </li>
      <li>www.quorv.com.au
        <svg class="contact-icon" viewBox="0 0 16 16" aria-hidden="true"><circle cx="8" cy="8" r="7.5" fill="var(--accent-orange)"/><path d="M4 4.5c1.5 0 2 1 3 1.5s.5 2-1 2.3S5 10 5.5 11.5M10 2.5c-.5 1.3.5 2 1.5 2.5s1.5 1.5.8 2.5M9.5 9.5c1 .2 2 1 1.8 2.5" stroke="#0b6b96" stroke-width="1.3" fill="none" stroke-linecap="round"/></svg>
      </li>
    </ul>
  </section>
</div>
</body>
</html>
```